Firm Stationery Design

I need a design for stationery, including: Stationery First Page, Stationery Second Sheet, Envelope, Mailing Label for Flat Envelopes, and Business Cards

```html
<!DOCTYPE html>
<html lang="en">
<head>
<meta charset="utf-8">
<title>Harlow Law LLC — Business Cards</title>
<link rel="stylesheet" href="https://fonts.googleapis.com/css2?family=Montserrat:wght@500;700;800&family=Roboto:wght@400;500&display=swap">
<style>
  :root {
    --orange: #ff9f00;
    --orange-deep: #f08c00;
    --ink: #1c1c1c;
    --paper: #ffffff;
    --rule: #cfcfcf;
    --text: #2a2a2a;
    --stage: #2b2b2b;
  }
  * { margin: 0; padding: 0; box-sizing: border-box; }
  html, body { width: 1200px; height: 874px; overflow: hidden; }
  body {
    background: var(--stage);
    font-family: "Roboto", sans-serif;
    position: relative;
  }
  .card {
    position: absolute;
    width: 580px;
    height: 330px;
    border-radius: 18px;
    overflow: hidden;
    box-shadow: 0 10px 30px rgba(0,0,0,.45);
  }
  /* back */
  .card--back {
    left: 310px; top: 70px;
    background: var(--orange);
    display: flex; flex-direction: column; align-items: center; justify-content: center;
  }
  .back-brand {
    font-family: "Montserrat", sans-serif;
    font-weight: 800;
    font-size: 50px;
    letter-spacing: 2px;
    color: var(--orange-deep);
  }
  .back-brand-sub {
    font-family: "Montserrat", sans-serif;
    font-weight: 800;
    font-size: 16px;
    letter-spacing: 14px;
    color: var(--orange-deep);
    margin-top: 6px;
  }
  /* front */
  .card--front {
    left: 310px; top: 470px;
    background: var(--paper);
  }
  .person { position: absolute; left: 36px; top: 96px; }
  .person-name {
    font-family: "Montserrat", sans-serif;
    font-weight: 700; font-size: 25px; color: var(--ink);
  }
  .person-title { font-size: 14px; color: var(--orange); margin-top: 2px; }
  .contact-rule {
    position: absolute; left: 36px; width: 250px; top: 160px;
    border-top: 1px solid var(--rule);
  }
  .contact { position: absolute; left: 36px; top: 168px; list-style: none; }
  .contact li {
    display: flex; align-items: center; gap: 8px;
    font-size: 16px; color: var(--text); line-height: 21px;
  }
  .contact svg { width: 13px; height: 13px; flex: none; }
  .brand { position: absolute; right: 40px; top: 70px; text-align: center; }
  .brand-mark {
    width: 26px; height: 26px; background: var(--orange);
    margin: 0 auto 10px;
  }
  .brand-name {
    font-family: "Montserrat", sans-serif;
    font-weight: 800; font-size: 38px; line-height: 44px; color: var(--ink); letter-spacing: 1px;
  }
  .brand-sub {
    font-family: "Montserrat", sans-serif;
    font-weight: 800; font-size: 13px; letter-spacing: 12px;
    color: var(--orange); margin-top: 4px;
  }
  .address {
    position: absolute; right: 40px; top: 210px; text-align right;
    text-align: right;
    font-size: 15px; color: var(--text); line-height: 20px;
    border-top: 1px solid var(--rule); padding-top: 8px; width: 230px;
  }
  .footer { position: absolute; left: 0; right: 0; bottom: 0; height: 52px; }
  .footer svg { position: absolute; inset: 0; width: 100%; height: 100%; }
  .footer-web {
    position: absolute; right: 40px; bottom: 12px;
    font-size: 16px; font-weight: 500; color: var(--paper);
  }
</style>
</head>
<body>
  <section class="card card--back" aria-label="Business card back">
    <div class="back-brand">HARLOW</div>
    <div class="back-brand-sub">LAW LLC</div>
  </section>

  <section class="card card--front" aria-label="Business card front">
    <div class="person">
      <div class="person-name">DANIEL BROOKS</div>
      <div class="person-title">President</div>
    </div>
    <div class="contact-rule"></div>
    <ul class="contact">
      <li><svg viewBox="0 0 16 16"><path fill="#ff9f00" d="M3 1l3 3-2 2c1 2 3 4 5 5l2-2 3 3-2 2C7 14 2 9 1 3z"/></svg>555-218-4096</li>
      <li><svg viewBox="0 0 16 16"><rect x="4" y="1" width="8" height="14" rx="1.5" fill="none" stroke="#ff9f00" stroke-width="1.6"/></svg>555-730-1182</li>
      <li><svg viewBox="0 0 16 16"><rect x="1" y="3" width="14" height="10" fill="#ff9f00"/><path d="M1 3l7 6 7-6" fill="none" stroke="#fff" stroke-width="1.3"/></svg>info@harlowlaw.com</li>
    </ul>

    <div class="brand">
      <div class="brand-mark"></div>
      <div class="brand-name">HARLOW</div>
      <div class="brand-sub">LAW LLC</div>
    </div>

    <div class="address">4120 Juniper Road<br>Halden, Canada 58213</div>

    <div class="footer">
      <svg viewBox="0 0 580 52" preserveAspectRatio="none">
        <polygon points="0,0 290,44 580,44 580,52 0,52" fill="#ff9f00"/>
        <polygon points="270,52 310,14 580,14 580,52" fill="#1c1c1c"/>
      </svg>
      <span class="footer-web">www.harlowlaw.com</span>
    </div>
  </section>
</body>
</html>
```